Vorn upkeep KT Solar Venture

Solar power system install
Services and maintenance
wiring, Rewinding and Renovation
Switch Board Upgrade
Power and lighting point
t doesn’t matter how much you spend on quality parts, your solar system will let you down if your design and installation are sub-par. Have your solar system tailored and installed by our Master Electrician and Bright Grid Guild Accredited team.

Target Market(s)

sales and installed

Industry/Entity Type

Solar install and retailer

Contact Information for Business Card

Name , Email, Phone Number ,Business address,

Font styles to use
Serif

Colors
0054AA
0677BA
7BADD7
CADEEF
E8F1F8

Requirements
Must have
• clear and bright
Nice to have
• new design
Should not have
• unclear pictures

```html
<!DOCTYPE html>
<html lang="en">
<head>
<meta charset="utf-8">
<title>Vorn upkeep KT Solar Venture — Business Card</title>
<link href="https://fonts.googleapis.com/css2?family=Roboto:wght@400;700&display=swap" rel="stylesheet">
<style>
  :root {
    --blue-deep: #0054AA;
    --blue-mid: #0677BA;
    --blue-soft: #7BADD7;
    --blue-pale: #CADEEF;
    --blue-mist: #E8F1F8;
    --green: #5FA833;
    --green-light: #7DB928;
    --sun: #F2B21C;
    --ink: #1c1c1c;
    --card-white: #f3f4f4;
    --backdrop: #2c2c2c;
  }
  * { margin: 0; padding: 0; box-sizing: border-box; }
  html, body {
    width: 1200px; height: 1138px; overflow: hidden;
    background: var(--backdrop);
    font-family: "Roboto", Arial, sans-serif;
  }
  .card {
    position: absolute;
    width: 622px; height: 375px;
    border-radius: 18px;
    overflow: hidden;
    background: linear-gradient(180deg, #f7f7f7 0%, var(--card-white) 70%, #e4e5e5 100%);
  }
  .card--front { left: 274px; top: 186px; }
  .card--back  { left: 276px; top: 608px; }

  /* brand lockup */
  .brand { position: absolute; display: flex; align-items: center; }
  .brand__dot {
    width: 96px; height: 96px; border-radius: 50%;
    background: var(--sun); flex: none;
  }
  .brand__name {
    color: var(--blue-deep);
    font-weight: 700;
    text-transform: uppercase;
    line-height: 1.12;
    letter-spacing: 1px;
  }
  .card--front .brand { left: 104px; top: 62px; gap: 26px; }
  .card--front .brand__name { font-size: 31px; }

  .services-band {
    position: absolute; left: 0; top: 239px; width: 100%; height: 74px;
    background: linear-gradient(90deg, var(--green) 0%, #2f9a78 40%, var(--blue-mid) 75%, #0a6ab0 100%);
    color: var(--blue-mist);
    font-size: 16.5px;
    text-align: center;
    display: flex; flex-direction: column; justify-content: center; gap: 6px;
  }
  .web-line {
    position: absolute; left: 0; top: 333px; width: 100%;
    display: flex; justify-content: center; align-items: center; gap: 24px;
    font-size: 15.5px; color: var(--ink);
  }
  .web-line__rule { width: 80px; height: 2px; }
  .web-line__rule--blue { background: linear-gradient(90deg, transparent, var(--blue-mid)); }
  .web-line__rule--green { background: linear-gradient(90deg, var(--green), transparent); }

  /* back */
  .back-shape { position: absolute; left: 0; top: 0; }
  .card--back .brand {
    left: 28px; top: 78px; width: 236px;
    flex-direction: column; gap: 22px; text-align: center;
  }
  .card--back .brand__dot { width: 104px; height: 104px; }
  .card--back .brand__name { font-size: 24px; }

  .person { position: absolute; left: 345px; top: 58px; }
  .person__name { color: var(--green-light); font-size: 25px; font-weight: 700; }
  .person__role { color: #fff; font-size: 16px; margin-top: 6px; }

  .address {
    position: absolute; left: 345px; top: 170px;
    color: #fff; font-size: 16px; line-height: 24px;
  }
  .contacts {
    position: absolute; left: 345px; top: 224px;
    list-style: none; color: #fff; font-size: 16px;
  }
  .contacts li { display: flex; align-items: center; height: 23.5px; }
  .contacts svg { width: 14px; height: 14px; margin: 0 17px 0 2px; flex: none; }

  .tag-band {
    position: absolute; left: 290px; top: 318px; width: 332px; height: 38px;
    background: linear-gradient(90deg, #3c9a3c 0%, var(--green-light) 100%);
    color: #fff; font-size: 16px;
    display: flex; align-items: center; padding-left: 55px;
  }
</style>
</head>
<body>

<section class="card card--front">
  <div class="brand">
    <span class="brand__dot"></span>
    <span class="brand__name">Vorn upkeep<br>KT Solar Venture</span>
  </div>
  <div class="services-band">
    <p>Solar Power System Install &nbsp;|&nbsp; Wiring, Rewinding &amp; Renovation</p>
    <p>Services &amp; Maintenance &nbsp;|&nbsp; Switch Board Upgrade &nbsp;|&nbsp; Power &amp; Lighting Point</p>
  </div>
  <div class="web-line">
    <span class="web-line__rule web-line__rule--blue"></span>
    <span>www.ktsolarventure.com</span>
    <span class="web-line__rule web-line__rule--green"></span>
  </div>
</section>

<section class="card card--back">
  <svg class="back-shape" width="622" height="375" viewBox="0 0 622 375" aria-hidden="true">
    <defs>
      <linearGradient id="panelBlue" x1="0" y1="0" x2="0" y2="1">
        <stop offset="0" stop-color="#0054AA"/>
        <stop offset="1" stop-color="#0677BA"/>
      </linearGradient>
    </defs>
    <path d="M236,0 H622 V375 H230 Q332,220 236,0 Z" fill="#5FA833"/>
    <path d="M244,0 H622 V375 H240 Q340,220 244,0 Z" fill="url(#panelBlue)"/>
  </svg>

  <div class="brand">
    <span class="brand__dot"></span>
    <span class="brand__name">Vorn upkeep<br>KT Solar Venture</span>
  </div>

  <div class="person">
    <h1 class="person__name">Aron Pell Marsh</h1>
    <p class="person__role">Managing Director</p>
  </div>

  <p class="address">87 Larkfield Rd., Dunmore,<br>Westvale, US 204718</p>

  <ul class="contacts">
    <li>
      <svg viewBox="0 0 14 14" aria-hidden="true"><path d="M1 5 Q7 0 13 5 L11 6.5 L9.5 5 H4.5 L3 6.5 Z M3.5 7 H10.5 L12 12.5 H2 Z" fill="#7DB928"/></svg>
      555-014-2790
    </li>
    <li>
      <svg viewBox="0 0 14 14" aria-hidden="true"><rect x="1" y="3" width="12" height="8.5" fill="#7DB928"/><path d="M1 3 L7 8 L13 3" stroke="#0677BA" stroke-width="1.2" fill="none"/></svg>
      aron@ktsolarventure.com
    </li>
    <li>
      <svg viewBox="0 0 14 14" aria-hidden="true"><circle cx="7" cy="7" r="6" fill="#7DB928"/><path d="M1 7 H13 M7 1 V13 M7 1 Q3 7 7 13 M7 1 Q11 7 7 13" stroke="#0677BA" stroke-width="0.9" fill="none"/></svg>
      www.ktsolarventure.com
    </li>
  </ul>

  <div class="tag-band">Solar power system install</div>
</section>

</body>
</html>
```